Retail Jewelry Business Card Design Project

We are in need of a new business card design for a retail jewelry store. This store is in the business of fine jewelry including but not specific to bridal jewelry, diamonds, designer jewelry and watches.

This store has been in business for 20 years but continues to strive for a modern professional appeal. The main colors use for this business are a royal blue, white and silver.

Target Market(s)

Target market is ages 18-50

Industry/Entity Type

Jewelry

Requirements
Must have
• Sales Person Name
Sales Person Email Address

Store Address
Store Phone
Website

Standard business card size. No odd shapes or sizes.
Nice to have
• Overall modern feel for card.

We have thought that a design with a nice feature of the logo on the back of the card would be nice but open to ideas.
Should not have
• No specific images of jewelry should be used.

```html
<!DOCTYPE html>
<html lang="en">
<head>
<meta charset="utf-8">
<title>Harlan Reed Fine Jewelry – Business Cards</title>
<link rel="stylesheet" href="https://fonts.googleapis.com/css2?family=Jost:wght@400;500;600&display=swap">
<style>
  :root {
    --royal-blue: #2e3192;
    --lavender: #8b86c9;
    --ink: #222226;
    --silver: #8a8a8e;
    --card: #ffffff;
    --backdrop: #e9e9ec;
  }
  * { box-sizing: border-box; margin: 0; padding: 0; }
  html, body {
    width: 1200px; height: 751px; overflow: hidden;
    background: var(--backdrop);
    font-family: "Jost", "Helvetica Neue", Arial, sans-serif;
  }
  .stage {
    position: relative; width: 1200px; height: 751px;
  }
  .card {
    position: absolute; top: 221px;
    width: 540px; height: 309px;
    background: var(--card);
    border-radius: 22px;
    overflow: hidden;
    box-shadow: 0 4px 14px rgba(0,0,0,0.12);
  }
  .card--front { left: 40px; }
  .card--back { left: 620px; }

  /* Front */
  .front-wave { position: absolute; inset: 0; width: 100%; height: 100%; }
  .front-brand {
    position: absolute; left: 36px; top: 108px; width: 240px;
    text-align: center; color: var(--royal-blue);
    font-weight: 500; font-size: 31px; line-height: 1.05;
  }
  .front-brand .brand-sub { font-size: 17px; letter-spacing: 3px; text-transform: uppercase; display: block; margin-top: 6px; }
  .divider {
    position: absolute; left: 292px; top: 58px; width: 1.5px; height: 118px;
    background: linear-gradient(to bottom, transparent, var(--silver) 20%, var(--silver) 80%, transparent);
  }
  .contact {
    position: absolute; left: 306px; top: 52px;
    color: var(--ink);
  }
  .contact-name {
    color: var(--royal-blue); font-weight: 600; font-size: 19px; margin-bottom: 14px;
  }
  .contact-list { list-style: none; font-size: 13px; }
  .contact-list li { display: flex; align-items: center; gap: 7px; margin-bottom: 7px; }
  .contact-list svg { width: 11px; height: 11px; flex: none; }
  .address {
    position: absolute; right: 26px; top: 226px;
    color: #fff; text-align: right; font-size: 13.5px; letter-spacing: 1px; line-height: 1.35;
  }

  /* Back */
  .back-brand {
    position: absolute; left: 0; right: 0; top: 92px;
    text-align: center; color: var(--ink);
    font-weight: 500; font-size: 52px; line-height: 1;
  }
  .back-brand .brand-sub { display: block; font-size: 25px; letter-spacing: 5px; text-transform: uppercase; margin-top: 12px; }
  .back-web {
    position: absolute; left: 0; right: 0; top: 232px;
    text-align: center; color: var(--ink); font-size: 13px; letter-spacing: 3px;
  }
</style>
</head>
<body>
<main class="stage">

  <section class="card card--front" aria-label="Business card front">
    <svg class="front-wave" viewBox="0 0 540 309" preserveAspectRatio="none" aria-hidden="true">
      <path d="M0,268 C160,236 320,176 540,182" fill="none" stroke="var(--lavender)" stroke-width="3"/>
      <path d="M0,282 C170,252 330,196 540,200 L540,309 L0,309 Z" fill="var(--royal-blue)"/>
    </svg>

    <h1 class="front-brand">Harlan Reed<span class="brand-sub">Fine Jewelry</span></h1>

    <div class="divider"></div>

    <div class="contact">
      <p class="contact-name">Harlan Reed Whitmore</p>
      <ul class="contact-list">
        <li>
          <svg viewBox="0 0 12 12" aria-hidden="true"><circle cx="6" cy="6" r="5" fill="none" stroke="var(--ink)" stroke-width="1.2"/><path d="M4.3,3.4 L5.2,3.4 L5.5,4.8 L4.9,5.3 Q5.6,6.7 6.8,7.2 L7.3,6.6 L8.6,7 L8.6,7.8 Q6,8.6 4.2,4.2 Z" fill="var(--ink)"/></svg>
          555-214-7730
        </li>
        <li>
          <svg viewBox="0 0 12 12" aria-hidden="true"><rect x="1" y="2.5" width="10" height="7" rx="1" fill="var(--ink)"/><path d="M1.5,3 L6,6.5 L10.5,3" fill="none" stroke="#fff" stroke-width="1"/></svg>
          harlan@harlanreedjewelry.com
        </li>
        <li>
          <svg viewBox="0 0 12 12" aria-hidden="true"><circle cx="6" cy="6" r="5" fill="none" stroke="var(--ink)" stroke-width="1.1"/><ellipse cx="6" cy="6" rx="2.2" ry="5" fill="none" stroke="var(--ink)" stroke-width="0.9"/><path d="M1,6 H11 M2,3.5 H10 M2,8.5 H10" stroke="var(--ink)" stroke-width="0.8"/></svg>
          www.harlanreedjewelry.com
        </li>
      </ul>
    </div>

    <address class="address">2870 Linden Avenue<br>Bayport, FL 32990</address>
  </section>

  <section class="card card--back" aria-label="Business card back">
    <h2 class="back-brand">Harlan Reed<span class="brand-sub">Fine Jewelry</span></h2>
    <p class="back-web">www.harlanreedjewelry.com</p>
  </section>

</main>
</body>
</html>
```